cleaning service

we are a cleaning company,

we have a current flyer but its very dull

I have attached it, can we make it look modern, maybe add pictures and colour

```html
<!DOCTYPE html>
<html lang="en">
<head>
<meta charset="utf-8">
<title>Cleaning Services by Marla's News</title>
<link rel="stylesheet" href="https://fonts.googleapis.com/css2?family=Oswald:wght@600;700&family=Roboto:wght@300;400&display=swap">
<style>
  :root {
    --ink: #111111;
    --brand-red: #9b1c1f;
    --sun-orange: #fbb117;
    --sun-yellow: #fdd314;
    --cream: #fdf0d6;
    --cream-light: #fef6e6;
    --offer-red: #b3183d;
    --offer-deep: #7e0f2a;
    --white: #ffffff;
  }
  html, body { margin: 0; padding: 0; overflow: hidden; }
  body { width: 849px; height: 1200px; }
  .flyer {
    position: relative;
    width: 849px;
    height: 1200px;
    overflow: hidden;
    background: linear-gradient(180deg, var(--white) 0, var(--white) 470px, var(--cream-light) 490px, var(--cream) 1200px);
    font-family: "Roboto", Arial, sans-serif;
    color: var(--ink);
  }
  .wave { position: absolute; left: 0; top: 0; }
  .title {
    position: absolute;
    left: 96px;
    top: 66px;
    margin: 0;
    font-family: "Oswald", "Arial Narrow", sans-serif;
    font-weight: 700;
    font-size: 46px;
    line-height: 55px;
    letter-spacing: -0.3px;
  }
  .title .light { color: var(--white); }
  .title .brand { color: var(--brand-red); }
  .hero-art {
    position: absolute;
    left: 359px;
    top: 103px;
    width: 404px;
    height: 307px;
    border-radius: 40px;
    background: radial-gradient(ellipse at 50% 55%, #f3a6cf 0, #b9c8ea 45%, rgba(185,200,234,0) 72%);
  }
  .copy {
    position: absolute;
    top: 466px;
    font-size: 17px;
    font-weight: 300;
    line-height: 22.7px;
    white-space: nowrap;
  }
  .copy p { margin: 0 0 14px; }
  .copy-left { left: 84px; }
  .copy-right { left: 441px; }
  .offer-art {
    position: absolute;
    left: 441px;
    top: 725px;
    width: 358px;
    height: 209px;
    border-radius: 50%;
    background: radial-gradient(ellipse at 50% 50%, var(--offer-red) 0, var(--offer-deep) 48%, rgba(126,15,42,0) 72%);
  }
  .cta {
    position: absolute;
    left: 191px;
    top: 1049px;
    width: 680px;
    height: 88px;
    border-radius: 44px 0 0 44px;
    background: linear-gradient(90deg, var(--cream-light) 0, #fde7bd 60%, #fbc45c 100%);
    box-shadow: 0 1px 3px rgba(200,140,30,0.35);
  }
  .cta-note {
    position: absolute;
    left: 47px;
    top: 21px;
    margin: 0;
    font-family: "Oswald", "Arial Narrow", sans-serif;
    font-weight: 600;
    font-size: 17.5px;
    line-height: 20px;
    white-space: nowrap;
  }
  .cta-call {
    position: absolute;
    left: 47px;
    top: 43px;
    margin: 0;
    font-family: "Oswald", "Arial Narrow", sans-serif;
    font-weight: 700;
    font-size: 28.5px;
    line-height: 34px;
    color: var(--brand-red);
    white-space: nowrap;
  }
</style>
</head>
<body>
<main class="flyer">
  <svg class="wave" width="849" height="1200" viewBox="0 0 849 1200" aria-hidden="true">
    <defs>
      <linearGradient id="sunGradient" x1="0" y1="0" x2="1" y2="0">
        <stop offset="0" stop-color="var(--sun-orange)"/>
        <stop offset="1" stop-color="var(--sun-yellow)"/>
      </linearGradient>
    </defs>
    <path d="M198,0 H849 V438 C805,420 785,335 745,262 C700,185 610,150 490,158 C385,165 300,140 262,92 C232,56 212,26 198,0 Z" fill="url(#sunGradient)"/>
    <path d="M0,1022 C38,1030 52,1080 72,1122 C102,1170 200,1168 268,1200 H0 Z" fill="url(#sunGradient)"/>
  </svg>

  <h1 class="title">CLEANING <span class="light">SERVICES</span><br>by <span class="brand">MARLA’S NEWS</span></h1>

  <div class="hero-art" role="img" aria-label="Illustration of two cleaners in pink shirts using a floor polisher and a vacuum cleaner"></div>

  <section class="copy copy-left">
    <p>Marla’s Cleaning Services offers professional<br>cleaning services to make your home look<br>its very best. From cleaning sinks, baths<br>and tiles to polishing windows, our<br>cleaners have the expertise to deal with<br>every cleaning challenge.</p>
    <p>Let me customise a cleaning service<br>programme to suit your individual needs<br>and your budget. Whether you require a<br>regular service (daily, weekly or monthly) or<br>just a one-off service, you can count on<br>Marla’s Cleaning services for a cleaning<br>service at excellent rates.</p>
    <p>In addition, Marla’s Cleaning Services<br>believes that the products we use really<br>matter. All the products we use are natural<br>and non-toxic, which makes them healthier<br>for your home and safer for the local<br>London environment. I have personally</p>
  </section>

  <section class="copy copy-right">
    <p>research all our house cleaning products to<br>ensure they are non-toxic, biodegradable<br>and not tested on animals.</p>
    <p>We can integrate the cleaning services<br>with the newspaper delivery services and<br>as well are offering a 20% off for all our<br>newspaper customers and £50 for<br>introducing us to your family and friends.</p>
  </section>

  <div class="offer-art" role="img" aria-label="Red ribbon badge reading 20% off special offer"></div>

  <aside class="cta">
    <p class="cta-note">Please turnover for our services and prices</p>
    <p class="cta-call">Please call us on 07700900417 to beat any price</p>
  </aside>
</main>
</body>
</html>
```